Vegan bakery needs business card

We need a business card design for my vegan bakery in Philadelphia Pa. We create amazing whole food plant based cuisine that is egg and dairy free. We use fruits, vegetables, healing herbs, nuts, natural sugars (date, turbinado, agave) and non bleached flours in our creations. Due to demand and interest in the Philadelphia area we created a late night vegan dessert delivery service named Bramble Vegan. We are the only business providing delicious vegan desserts delivered to your door at 1am!! We would like to see designs that use the color scheme in the logo. The final design should communicate the benefits of our products: dairy/egg free, plant based, healing herbs, amazing food.

```html
<!DOCTYPE html>
<html lang="en">
<head>
<meta charset="utf-8">
<title>Bramble Vegan – Business Card</title>
<link href="https://fonts.googleapis.com/css2?family=Questrial&display=swap" rel="stylesheet">
<style>
  :root{
    --stage:#2a2a2c;
    --card-dark:#0e1019;
    --card-light:#ffffff;
    --coral:#f0775a;
    --leaf:#6cc04a;
    --ink:#7a7a7a;
    --divider:#9fd27f;
  }
  *{margin:0;padding:0;box-sizing:border-box}
  html,body{width:1200px;height:880px;overflow:hidden;background:var(--stage)}
  body{position:relative;font-family:"Questrial",sans-serif}

  .card{position:absolute;width:600px;height:343px;border-radius:22px;box-shadow:0 12px 30px rgba(0,0,0,.45)}
  .card--front{left:120px;top:80px;background:var(--card-dark)}
  .card--back{left:480px;top:470px;background:var(--card-light)}

  .brand{display:flex;align-items:center;gap:10px;color:var(--coral);font-size:34px;letter-spacing:.5px;white-space:nowrap}
  .brand__dot{width:14px;height:14px;border-radius:50%;background:var(--leaf)}

  .card--front .brand{position:absolute;left:0;right:0;top:110px;justify-content:center}
  .products{position:absolute;left:0;right:0;top:205px;text-align:center}
  .products__title{color:var(--leaf);font-size:15px;letter-spacing:.5px;margin-bottom:8px}
  .products__list{color:var(--coral);font-size:16px}

  .back__logo{position:absolute;left:40px;top:120px;width:220px}
  .back__logo .brand{font-size:30px}
  .claims{margin-top:18px;margin-left:70px;color:var(--leaf);font-size:19px;line-height:1.05}

  .divider{position:absolute;left:275px;top:70px;width:1.5px;height:200px;background:var(--divider)}

  .contact{position:absolute;left:305px;top:78px;color:var(--ink)}
  .contact__name{color:var(--coral);font-size:22px}
  .contact__role{font-size:14px;margin-bottom:26px}
  .contact__address{font-size:14px;line-height:1.35;margin-bottom:14px}
  .contact__list{list-style:none;font-size:14px}
  .contact__list li{display:flex;align-items:center;gap:8px;line-height:1.45}
  .contact__icon{width:14px;height:14px;flex:none}
</style>
</head>
<body>

<section class="card card--front" aria-label="Card front">
  <div class="brand"><span class="brand__dot"></span>Bramble Vegan</div>
  <div class="products">
    <p class="products__title">OUR PRODUCTS</p>
    <p class="products__list">dairy/egg free, plant based, healing herbs, amazing food.</p>
  </div>
</section>

<section class="card card--back" aria-label="Card back">
  <div class="back__logo">
    <div class="brand"><span class="brand__dot"></span>Bramble Vegan</div>
    <p class="claims">100% vegan<br>100% delicious</p>
  </div>

  <div class="divider"></div>

  <div class="contact">
    <p class="contact__name">Nora Ellis</p>
    <p class="contact__role">Director of Marketing</p>
    <p class="contact__address">Po Box 456, Orchard Street<br>Philadelphia, PA 19106</p>
    <ul class="contact__list">
      <li>
        <svg class="contact__icon" viewBox="0 0 14 14" aria-hidden="true"><circle cx="7" cy="7" r="7" fill="var(--coral)"/><path d="M4.5 3.5l1.5 0 .6 1.8-.9.7a5 5 0 0 0 2.3 2.3l.7-.9 1.8.6v1.5c-3.5.3-6.3-2.5-6-6z" fill="#fff"/></svg>
        215-555-0142
      </li>
      <li>
        <svg class="contact__icon" viewBox="0 0 14 14" aria-hidden="true"><circle cx="7" cy="7" r="7" fill="var(--coral)"/><rect x="3.5" y="4.5" width="7" height="5" fill="none" stroke="#fff" stroke-width="1"/><path d="M3.5 4.5L7 7.3l3.5-2.8" fill="none" stroke="#fff" stroke-width="1"/></svg>
        info@bramblevegan.com
      </li>
      <li>
        <svg class="contact__icon" viewBox="0 0 14 14" aria-hidden="true"><circle cx="7" cy="7" r="7" fill="var(--coral)"/><circle cx="7" cy="7" r="3.5" fill="none" stroke="#fff" stroke-width="1"/><path d="M3.5 7h7M7 3.5c-1.5 2-1.5 5 0 7M7 3.5c1.5 2 1.5 5 0 7" fill="none" stroke="#fff" stroke-width=".8"/></svg>
        www.bramblevegan.com
      </li>
    </ul>
  </div>
</section>

</body>
</html>
```